Bramblewick Forage Business Cards

I need a business card with my logo, number, Facebook account, and some information about what I am selling. Green card with logo on the front. 555-214-8392 phone number, @bramblewickforage Facebook, •Orchardgrass Hay •Alfalfa Hay •Mixed Grass Hay , and “Premium Quality Hay” all written on the back.

Target Market(s)

Hay

Contact Information for Business Card

Phone number, Facebook, different types of hay.

Colors
00AB8E
00BBA5
67D7C9
C6EFE9
E9F9F6

```html
<!DOCTYPE html>
<html lang="en">
<head>
<meta charset="UTF-8">
<title>Bramblewick Forage Business Cards</title>
<link rel="stylesheet" href="https://fonts.googleapis.com/css2?family=Open+Sans:wght@400;600;700&family=Roboto:wght@700&family=Yellowtail&display=swap">
<style>
  :root {
    --stage: #d5d7d9;
    --brand-green: #00963f;
    --ink: #1a1a1a;
    --paper: #ffffff;
  }
  * { margin: 0; padding: 0; box-sizing: border-box; }
  html, body { width: 1187px; height: 1200px; overflow: hidden; }
  body { background: var(--stage); position: relative; font-family: "Open Sans", sans-serif; }

  .card {
    position: absolute;
    left: 215px;
    width: 758px;
    height: 432px;
    border-radius: 18px;
    overflow: hidden;
  }
  .card--front { top: 122px; background: var(--brand-green); }
  .card--back { top: 644px; background: var(--paper); }

  .front-mark {
    position: absolute;
    left: 0; right: 0; top: 190px;
    display: flex; align-items: center; justify-content: center; gap: 18px;
  }
  .front-mark__dot { width: 34px; height: 34px; border-radius: 50%; background: var(--paper); }
  .front-mark__name { color: var(--paper); font-weight: 700; font-size: 46px; letter-spacing: 0.5px; }

  .back-mark {
    position: absolute; left: 42px; top: 168px;
    display: flex; align-items: center; gap: 16px;
  }
  .back-mark__dot { width: 62px; height: 62px; border-radius: 50%; background: var(--brand-green); flex: none; }
  .back-mark__name { color: var(--ink); font-weight: 700; font-size: 28px; line-height: 1; }
  .back-mark__tagline { margin-top: 12px; color: var(--ink); font-weight: 700; font-size: 17px; letter-spacing: 0.6px; padding-left: 20px; }

  .contact { position: absolute; left: 498px; top: 152px; }
  .contact__name { font-family: "Yellowtail", cursive; color: var(--brand-green); font-size: 40px; line-height: 1.1; }
  .contact__phone { font-family: "Roboto", sans-serif; font-weight: 700; font-size: 31px; color: var(--ink); margin-top: 8px; }
  .contact__social { display: flex; align-items: center; gap: 6px; margin-top: 4px; font-size: 18px; color: var(--ink); letter-spacing: 0.4px; }
  .contact__social-dot { width: 22px; height: 22px; border-radius: 50%; background: var(--brand-green); }

  .products {
    position: absolute; left: 0; right: 0; top: 348px;
    display: flex; justify-content: center; gap: 12px;
    list-style: none; font-size: 20px; color: var(--ink); letter-spacing: 0.3px;
  }
  .products li { display: flex; align-items: center; gap: 6px; }
  .products li::before { content: ""; width: 10px; height: 10px; border-radius: 50%; background: var(--brand-green); }

  .card__band { position: absolute; left: 0; right: 0; bottom: 0; height: 13px; background: var(--brand-green); }
</style>
</head>
<body>
  <section class="card card--front">
    <div class="front-mark">
      <span class="front-mark__dot"></span>
      <span class="front-mark__name">Bramblewick Forage</span>
    </div>
  </section>

  <section class="card card--back">
    <div class="back-mark">
      <span class="back-mark__dot"></span>
      <div>
        <div class="back-mark__name">Bramblewick Forage</div>
        <div class="back-mark__tagline">“Premium Quality Hay”</div>
      </div>
    </div>

    <div class="contact">
      <div class="contact__name">Dale Harwick</div>
      <div class="contact__phone">555-214-8392</div>
      <div class="contact__social"><span class="contact__social-dot"></span>@bramblewickforage</div>
    </div>

    <ul class="products">
      <li>Orchardgrass Hay</li>
      <li>Alfalfa Hay</li>
      <li>Mixed Grass Hay</li>
    </ul>

    <div class="card__band"></div>
  </section>
</body>
</html>
```